Larkmoor Drones Business Card

We are a new company based in Central Queensland, Australia that uses specalised drones (Voskel Ferra Q80) to undertake mainly agricultural operations, like spraying weeds, spraying crops, spreading seed etc. I have attached a Plimbo proof of a card I was thinking along the lines of - purely a start point. The drone used in the business card MUST be a Voskel Ferra Q80.
I am very open to other ideas, especially fonts and layout. I don't have website etc set up yet.
The images are stock and easily interchangeable, I just ask that any background images reflect the local central Queensland area. The photo of the drone is not even complete (propellers cut off) and I need a new stock photo – I’m not sure if this is an issue, or I can pay for an image if need be. PLEASE FIND AN FERRA Q80 image - 4 sprayers, not 6.
The logo/business name is very draft and looking for further ideas, ideally incorporating drones or agriculture design elements into the design of the business name. The business name needs work on the graphic/design – it is a draft that I have included, the drone propellers (being a different colour) are DRAFT only and intended for changes. PLEASE DO NOT USE THE DRONE PORPELLER I HAVE USED AS A DRAFT. TRY TO FIND SOMETHING ELSE.. The arrow is a shape and not aligned in any way, I would also like ideas on different fonts and additional elements, like air streams, aviation elements, aviation or country western (farming like) themes and fonts etc.
Ideally looking at staying within the blue, green and yellow colours, keeping with an natural, outdoorsy, environmental feel.

Target Market(s)

Farmers, Agriculture, Local Governments, Land Managers

Industry/Entity Type

Agriculture, Drones, Aviation

Contact Information for Business Card

Agricultural Drone (Voskel Ferra Q80), Farming, Business Name.

Font styles to use
Sans Serif

Colors
0054AA
0677BA
7BADD7
CADEEF
E8F1F8
0094D4
00A9DD
6FCCEA
C7EBF8
E9F6FB
00AB8E
00BBA5
67D7C9
C6EFE9
E9F9F6
59FF00
82FF00
B8FF75
E3FFCB
F4FFEA

Requirements
Must have
• Voskel Ferra Q80 Drone
Should not have
• Tractors

```html
<!DOCTYPE html>
<html lang="en">
<head>
<meta charset="utf-8">
<title>Larkmoor Drones – Business Card</title>
<link rel="stylesheet" href="https://fonts.googleapis.com/css2?family=Poppins:wght@400;500;700&family=Merriweather:wght@900&display=swap">
<style>
  :root {
    --backdrop: #1d1d1f;
    --card-white: #ffffff;
    --sky-deep: #0677BA;
    --sky-light: #6FCCEA;
    --field-green: #4e8f2a;
    --field-dark: #3a7420;
    --brand-teal: #00AB8E;
    --brand-green: #3fae29;
    --brand-blue: #0094D4;
    --accent-yellow: #e6c80f;
    --ink: #1a1a1a;
  }
  * { margin: 0; padding: 0; box-sizing: border-box; }
  html, body { width: 1200px; height: 1015px; overflow: hidden; }
  body { background: var(--backdrop); font-family: "Poppins", sans-serif; position: relative; }

  .card {
    position: absolute;
    left: 240px;
    width: 720px;
    height: 412px;
    overflow: hidden;
    box-shadow: 0 12px 30px rgba(0,0,0,.55);
  }
  .card--front { top: 62px; }
  .card--back { top: 541px; background: var(--card-white); }

  .photo-fill {
    position: absolute; inset: 0;
    background: linear-gradient(180deg, var(--sky-deep) 0%, var(--sky-light) 34%, #9fc7a0 40%, var(--field-green) 52%, var(--field-dark) 100%);
  }

  .brand-name {
    font-family: "Poppins", sans-serif;
    font-weight: 500;
    line-height: .95;
    letter-spacing: 2px;
    text-transform: uppercase;
  }
  .card--front .brand {
    position: absolute; left: 190px; top: 130px; width: 340px; text-align: center;
    color: var(--card-white);
  }
  .card--front .brand-name { font-size: 56px; }

  .services {
    position: absolute; left: 0; right: 0; bottom: 42px; text-align: center;
    font-family: "Merriweather", serif; font-weight: 900; font-size: 22px;
    color: var(--card-white); letter-spacing: .3px;
  }
  .services .dot { color: var(--accent-yellow); padding: 0 8px; }

  .back-art { position: absolute; inset: 0; }

  .details {
    position: absolute; left: 410px; top: 40px; width: 295px; text-align: center; color: var(--ink);
  }
  .details .brand-name { font-size: 46px; color: var(--brand-teal); }
  .region {
    margin-top: 10px; font-family: "Merriweather", serif; font-weight: 900;
    font-size: 11px; letter-spacing: .4px; text-transform: uppercase;
  }
  .person { margin-top: 22px; font-weight: 700; font-size: 22px; color: var(--brand-green); text-transform: uppercase; line-height: 1.1; }
  .role { font-size: 15px; line-height: 1.2; }
  .rule { width: 70px; height: 1px; background: var(--ink); margin: 10px auto 12px; }
  .contact { font-size: 15px; line-height: 1.35; }
  .contact .web { color: var(--brand-blue); }
</style>
</head>
<body>

<section class="card card--front">
  <div class="photo-fill" role="img" aria-label="Photo of an agricultural spray drone hovering over green Central Queensland farmland under a blue sky"></div>
  <div class="brand">
    <div class="brand-name">Larkmoor<br>Drones</div>
  </div>
  <p class="services">Spraying Weeds<span class="dot">•</span>Spraying Crops<span class="dot">•</span>Spreading Seeds</p>
</section>

<section class="card card--back">
  <svg class="back-art" viewBox="0 0 720 412" width="720" height="412">
    <defs>
      <linearGradient id="field-photo" x1="0" y1="0" x2="0" y2="1">
        <stop offset="0" stop-color="#0677BA"/>
        <stop offset=".3" stop-color="#6FCCEA"/>
        <stop offset=".38" stop-color="#9fc7a0"/>
        <stop offset=".5" stop-color="#4e8f2a"/>
        <stop offset="1" stop-color="#3a7420"/>
      </linearGradient>
    </defs>
    <path d="M0 412 V0 H250 C395 90 415 320 260 412 Z" fill="#e6c80f" transform="translate(10 0)"/>
    <path d="M0 412 V0 H250 C395 90 415 320 260 412 Z" fill="url(#field-photo)" role="img" aria-label="Photo of a spray drone flying low over green cropland"/>
  </svg>

  <div class="details">
    <div class="brand-name">Larkmoor<br>Drones</div>
    <p class="region">Servicing Central Queensland</p>
    <p class="person">Dorian Pellow</p>
    <p class="role">Managing Director</p>
    <div class="rule"></div>
    <p class="contact">044-555 017 342<br>info@larkmoormail.com<br>www.<span class="web">larkmoorsite</span>.com</p>
  </div>
</section>

</body>
</html>
```